Indoor Air Restoration company needs graphic design for a 6x12 v nose trailer to wrap

We offer mold services, duct cleaning, water damage clean up and odor removal. "We find, fix and prevent mold, odor and allergen problems" is what we want to communicate on this trailer, which is a rolling billboard. We like the blue and orange color themes, as found in our logo. The company name is Brightwater Dwelling Services and the logo is attached below. We'd like to see our message clearly, company name and what we offer. We tend to lean towards white letters on a darker background (blue or orange) but are very open to outside ideas, as we are stuck! Our website is available for reference if that is helpful. www.brightwaterdwell.com The phone number to be printed on truck is 302-517-9046, Happy designing!!

Target Market(s)

Home owners

Industry/Entity Type

Indoor Air Quality, Mold Remediation

Font styles to use
Sans Serif

Colors
0054AA
0677BA
7BADD7
CADEEF
E8F1F8
F0912C
F2A743
F7CA91
FBE8D2
FDF5EE

Requirements
Must have
• our message, company name and phone
Nice to have
• services we offer (mold remediation, duct cleaning, water damage and odor removal
Should not have
• cartoon feel

```html
<!DOCTYPE html>
<html lang="en">
<head>
<meta charset="utf-8">
<title>Brightwater Dwelling Services – Trailer Wrap</title>
<link rel="stylesheet" href="https://fonts.googleapis.com/css2?family=Oswald:wght@500;600&family=Montserrat:wght@600;700&display=swap">
<style>
  :root {
    --page: #ffffff;
    --panel-blue-light: #2356a8;
    --panel-blue-dark: #142d66;
    --ink-dark: #0a101f;
    --brand-blue: #1b7cc4;
    --white: #ffffff;
    --water-a: #1559a8; --water-b: #25a0d8;
    --mold-a: #177a3a; --mold-b: #6db346;
    --odor-a: #7a1219; --odor-b: #de1b2d;
    --ducts-a: #e84b27; --ducts-b: #f4a843;
    --band-orange-a: #e84e27; --band-orange-b: #f3ab46;
    --band-green-a: #117336; --band-green-b: #6cb345;
    --accent-pink: rgba(190, 70, 110, 0.35);
    --accent-red: rgba(200, 40, 55, 0.45);
  }
  * { margin: 0; padding: 0; box-sizing: border-box; }
  html, body { width: 1018px; height: 1200px; overflow: hidden; background: var(--page); }
  .canvas { position: relative; width: 1018px; height: 1200px; }

  .wrap-panel {
    position: absolute; left: 123px; top: 178px; width: 780px; height: 876px;
    overflow: hidden;
    background: linear-gradient(135deg, var(--panel-blue-light) 0%, #1d4592 45%, var(--panel-blue-dark) 100%);
  }
  .accent-shape { position: absolute; border-radius: 26px; transform: rotate(45deg); }
  .accent-left-big { left: -190px; top: 150px; width: 300px; height: 300px; background: var(--accent-pink); }
  .accent-left-small { left: 30px; top: 340px; width: 80px; height: 80px; background: rgba(200, 80, 110, 0.35); }
  .accent-top-right { left: 500px; top: -120px; width: 300px; height: 300px; background: rgba(150, 40, 70, 0.45); }
  .accent-top-dark { left: 380px; top: -180px; width: 280px; height: 280px; background: rgba(60, 20, 50, 0.55); border-radius: 0; }
  .accent-bottom-right { left: 560px; top: 700px; width: 320px; height: 320px; background: var(--accent-red); }

  .brand-diamond { position: absolute; left: 0; top: 0; }

  .brand-name {
    position: absolute; left: 0; width: 780px; top: 200px; text-align: center;
    font-family: "Oswald", sans-serif; font-weight: 600; color: var(--brand-blue);
    text-transform: uppercase; line-height: 1.05;
  }
  .brand-name .line-main { display: block; font-size: 44px; letter-spacing: 1px; }
  .brand-name .line-sub { display: block; font-size: 26px; letter-spacing: 4px; margin-top: 4px; }

  .message-box {
    position: absolute; left: 78px; top: 474px; width: 630px; height: 230px;
    background: var(--ink-dark); border-radius: 24px;
  }
  .headline {
    position: absolute; left: 0; width: 630px; top: 22px; text-align: center;
    font-family: "Oswald", sans-serif; font-weight: 600; font-size: 40px;
    letter-spacing: 7px; color: var(--white); text-transform: uppercase;
  }
  .service-row { position: absolute; left: 88px; top: 75px; display: flex; gap: 19px; }
  .service-tile {
    width: 97px; height: 97px; border-radius: 16px;
    display: flex; flex-direction: column; align-items: center;
    font-family: "Oswald", sans-serif; font-weight: 500; font-size: 26px;
    color: var(--white); text-transform: uppercase; padding-top: 2px;
  }
  .service-tile .tile-mark { width: 34px; height: 34px; border-radius: 50%; border: 4px solid var(--white); margin-top: 10px; }
  .tile-water { background: linear-gradient(135deg, var(--water-a), var(--water-b)); }
  .tile-mold { background: linear-gradient(135deg, var(--mold-a), var(--mold-b)); }
  .tile-odor { background: linear-gradient(135deg, var(--odor-a), var(--odor-b)); }
  .tile-ducts { background: linear-gradient(135deg, var(--ducts-a), var(--ducts-b)); }

  .contact-band { position: absolute; border-radius: 24px; display: flex; align-items: center; color: var(--white); font-family: "Montserrat", sans-serif; }
  .band-web { left: 69px; top: 723px; width: 696px; height: 79px; background: linear-gradient(90deg, var(--band-green-a), var(--band-green-b)); }
  .band-phone { left: 19px; top: 666px; width: 667px; height: 80px; background: linear-gradient(90deg, var(--band-orange-a), var(--band-orange-b)); }
  .band-icon { position: absolute; }
  .band-phone .band-icon { left: 249px; top: 21px; }
  .band-web .band-icon { left: 199px; top: 21px; }
  .phone-number { position: absolute; left: 315px; top: 8px; font-size: 50px; font-weight: 700; letter-spacing: -1px; }
  .web-address { position: absolute; left: 265px; top: 20px; font-size: 27px; font-weight: 700; letter-spacing: -0.5px; }
</style>
</head>
<body>
<div class="canvas">
  <section class="wrap-panel" aria-label="Trailer wrap side panel">
    <div class="accent-shape accent-top-dark"></div>
    <div class="accent-shape accent-left-big"></div>
    <div class="accent-shape accent-left-small"></div>
    <div class="accent-shape accent-top-right"></div>
    <div class="accent-shape accent-bottom-right"></div>

    <svg class="brand-diamond" width="780" height="876" viewBox="0 0 780 876" aria-hidden="true">
      <path d="M351 0 L520 0 L720 200 Q745 225 720 250 L420 540 Q388 570 356 540 L61 250 Q36 225 61 200 L261 0 Z" fill="#0a101f"/>
    </svg>

    <h1 class="brand-name">
      <span class="line-main">Brightwater</span>
      <span class="line-sub">Dwelling Services</span>
    </h1>

    <div class="message-box">
      <p class="headline">We find, fix and prevent</p>
      <div class="service-row">
        <div class="service-tile tile-water">Water<span class="tile-mark"></span></div>
        <div class="service-tile tile-mold">Mold<span class="tile-mark"></span></div>
        <div class="service-tile tile-odor">Odor<span class="tile-mark"></span></div>
        <div class="service-tile tile-ducts">Ducts<span class="tile-mark"></span></div>
      </div>
    </div>

    <div class="contact-band band-web">
      <svg class="band-icon" width="38" height="38" viewBox="0 0 38 38" aria-hidden="true">
        <circle cx="19" cy="19" r="16" fill="none" stroke="#fff" stroke-width="2.5"/>
        <ellipse cx="19" cy="19" rx="7" ry="16" fill="none" stroke="#fff" stroke-width="2.5"/>
        <line x1="3" y1="19" x2="35" y2="19" stroke="#fff" stroke-width="2.5"/>
      </svg>
      <span class="web-address">brightwaterdwell.com</span>
    </div>

    <div class="contact-band band-phone">
      <svg class="band-icon" width="38" height="38" viewBox="0 0 38 38" aria-hidden="true">
        <circle cx="19" cy="19" r="18" fill="#e9eef3"/>
        <path d="M13 10 q-3 2 -1 8 q3 7 9 9 q5 1 6 -2 l-3 -3 q-2 1 -3 0 q-4 -2 -5 -6 q0 -1 1 -2 z" fill="#e84e27"/>
      </svg>
      <span class="phone-number">302-517-9046</span>
    </div>
  </section>
</div>
</body>
</html>
```